New Innovative Counselling and psychotherapy Service needs Business Card design

Keep it simple and professional. On one side, just company name and logo (perhaps in all blue) and maybe a tag line.

On other side (all white) my name and Qualifications in centre

Industry/Entity Type

Health And Wellness

Contact Information for Business Card

Dara Whelby
Counsellor & Psychotherapist
BSc (Psychol.), BA, Dip. (Couns. & Psych.), PG.Cert (CBT), FGTrK, ONRE

I will also require Mobile no, Email and web site address of which I'll pass on to final designer.

Font styles to use
Sans Serif

Requirements
Must have
• My Logo Only and please use the colours in logo that is in it.
Should not have
• Any other images

```html
<!DOCTYPE html>
<html lang="en">
<head>
<meta charset="UTF-8">
<title>ClearHaven Business Card</title>
<link rel="stylesheet" href="https://fonts.googleapis.com/css2?family=Montserrat:wght@400;500&family=Open+Sans:wght@400;600&display=swap">
<style>
  :root {
    --backdrop: #2b2b2b;
    --card: #1d1d1e;
    --card-edge: #262627;
    --ink: #f2f2f2;
    --brand-blue: #3ab0e8;
    --brand-green: #7cc243;
    --emboss-light: #d9d9d9;
    --emboss-dark: #1a1a1a;
  }
  * { box-sizing: border-box; margin: 0; padding: 0; }
  html, body {
    width: 1200px; height: 900px; overflow: hidden;
    background: var(--backdrop);
  }
  .canvas {
    position: relative; width: 1200px; height: 900px;
    background: var(--backdrop);
  }
  .card {
    position: absolute;
    width: 640px; height: 366px;
    background: var(--card);
    border: 1px solid var(--card-edge);
    box-shadow: 0 12px 30px rgba(0,0,0,0.45);
    color: var(--ink);
    font-family: "Open Sans", sans-serif;
  }
  .card--front { left: 300px; top: 50px; }
  .card--back { left: 260px; top: 470px; overflow: hidden; }

  .brand {
    display: flex; align-items: center; gap: 16px;
  }
  .brand__dot {
    width: 52px; height: 52px; border-radius: 50%;
    background: var(--brand-blue);
  }
  .brand__name {
    font-family: "Montserrat", sans-serif;
    font-weight: 400;
    color: var(--ink);
    letter-spacing: 1px;
  }
  .card--front .brand {
    position: absolute; left: 50%; top: 130px; transform: translateX(-50%);
  }
  .card--front .brand__name { font-size: 38px; }

  .web {
    font-family: "Montserrat", sans-serif;
    font-size: 15px; letter-spacing: 0.5px; color: var(--ink);
  }
  .web__domain { color: var(--brand-green); }
  .card--front .web {
    position: absolute; bottom: 24px; left: 0; right: 0; text-align: center;
  }

  .card--back .brand {
    position: absolute; left: 42px; top: 34px; gap: 12px;
  }
  .card--back .brand__dot { width: 36px; height: 36px; }
  .card--back .brand__name { font-size: 26px; }

  .person {
    position: absolute; left: 42px; top: 118px;
  }
  .person__name {
    font-family: "Montserrat", sans-serif;
    font-weight: 500; font-size: 32px;
    color: var(--brand-blue); line-height: 1.1;
  }
  .person__role, .person__quals {
    font-size: 15px; line-height: 1.4; letter-spacing: 0.4px;
  }
  .person__quals { width: 270px; }

  .contact {
    position: absolute; left: 42px; top: 262px;
    list-style: none; font-size: 16px; line-height: 1.65;
  }
  .contact__item { display: flex; align-items: center; gap: 10px; }
  .contact__icon { width: 13px; height: 13px; flex: none; }

  .decor {
    position: absolute; right: 50px; top: 60px;
    width: 250px; height: 250px; border-radius: 50%;
    background: radial-gradient(circle at 75% 60%, var(--emboss-light), #6f6f6f 45%, var(--emboss-dark) 90%);
  }
</style>
</head>
<body>
<main class="canvas">

  <section class="card card--front" aria-label="Business card front">
    <div class="brand">
      <span class="brand__dot"></span>
      <span class="brand__name">ClearHaven</span>
    </div>
    <p class="web">www.<span class="web__domain">clearhaven</span>.com</p>
  </section>

  <section class="card card--back" aria-label="Business card back">
    <div class="brand">
      <span class="brand__dot"></span>
      <span class="brand__name">ClearHaven</span>
    </div>

    <div class="person">
      <h1 class="person__name">DARA WHELBY</h1>
      <p class="person__role">Counsellor &amp; Psychotherapist</p>
      <p class="person__quals">BSc (Psychol.), BA, Dip. (Couns. &amp; Psych.), PG.Cert (CBT), FGTrK, ONRE</p>
    </div>

    <ul class="contact">
      <li class="contact__item">
        <svg class="contact__icon" viewBox="0 0 24 24" aria-hidden="true"><path fill="#3ab0e8" d="M6.6 10.8a15 15 0 0 0 6.6 6.6l2.2-2.2a1 1 0 0 1 1-.25 11.4 11.4 0 0 0 3.6.57 1 1 0 0 1 1 1V20a1 1 0 0 1-1 1A17 17 0 0 1 3 4a1 1 0 0 1 1-1h3.5a1 1 0 0 1 1 1c0 1.25.2 2.45.57 3.6a1 1 0 0 1-.25 1z"/></svg>
        <span>555-014-2870</span>
      </li>
      <li class="contact__item">
        <svg class="contact__icon" viewBox="0 0 24 24" aria-hidden="true"><rect x="2" y="5" width="20" height="14" rx="1.5" fill="none" stroke="#3ab0e8" stroke-width="2"/><path d="M2 6l10 7 10-7" fill="none" stroke="#3ab0e8" stroke-width="2"/></svg>
        <span>info@clearhaven.com</span>
      </li>
      <li class="contact__item">
        <svg class="contact__icon" viewBox="0 0 24 24" aria-hidden="true"><circle cx="12" cy="12" r="10" fill="none" stroke="#3ab0e8" stroke-width="2"/><path d="M2 12h20M12 2c3 3 3 17 0 20M12 2c-3 3-3 17 0 20" fill="none" stroke="#3ab0e8" stroke-width="2"/></svg>
        <span class="web">www.<span class="web__domain">clearhaven</span>.com</span>
      </li>
    </ul>

    <div class="decor" role="img" aria-label="Large embossed brand emblem"></div>
  </section>

</main>
</body>
</html>
```